Thornvale Group needs a business card design

We need a new business card design using the logo recently selected in a logo competition on Pixel Bazaar. Our business is a consultancy specializing in aviation and energy and the winning business card design will promote an image of precision and professionalism with creativity.

Please use the logo with the name on the front of the card and use a complementary font. Make the back white with either the light grey or dark grey logo.

Target Market(s)

Senior finance and legal leaders at aviation and energy companies

Industry/Entity Type

Management Consulting

Contact Information for Business Card

Peter Castrell
President
Thornvale Group

www.thornvalegroup.example

(555) 204-6391
pc@thornvalegroup.example

Requirements
Must have
• Professional font that goes well with the logo font

```html
<!DOCTYPE html>
<html lang="en">
<head>
<meta charset="utf-8">
<title>Thornvale Group – Business Card</title>
<link rel="stylesheet" href="https://fonts.googleapis.com/css2?family=Open+Sans:wght@400;600;700&display=swap">
<style>
  :root {
    --page-bg: #e9e7e4;
    --front-dark: #3c3f42;
    --front-mid: #8e9396;
    --front-light: #b7bbbe;
    --swoosh: #dfe1ec;
    --swoosh-edge: #c3c6d6;
    --brand-blue: #2f7fbf;
    --ink-navy: #1f4a78;
    --white: #ffffff;
    --back-top: #f1f1f7;
    --back-bottom: #cfd1e4;
  }
  * { box-sizing: border-box; margin: 0; padding: 0; }
  html, body {
    width: 1200px; height: 913px; overflow: hidden;
    background: var(--page-bg);
    font-family: "Open Sans", Arial, sans-serif;
  }
  .canvas { position: relative; width: 1200px; height: 913px; }
  .card {
    position: absolute; width: 520px; height: 300px;
    border-radius: 18px; overflow: hidden;
    box-shadow: 0 6px 18px rgba(0,0,0,0.18);
  }
  /* Front */
  .card-front {
    left: 70px; top: 150px;
    background: linear-gradient(160deg, var(--front-light) 0%, var(--front-mid) 40%, var(--front-dark) 100%);
  }
  .card-front .swoosh { position: absolute; inset: 0; width: 100%; height: 100%; }
  .holder { position: absolute; right: 30px; top: 26px; text-align: right; }
  .holder-name { color: var(--brand-blue); font-weight: 700; font-size: 24px; line-height: 1.1; }
  .holder-title { color: var(--white); font-size: 14px; font-weight: 400; }
  .front-brand {
    position: absolute; left: 40px; top: 150px;
    color: var(--white); font-weight: 400; font-size: 30px; letter-spacing: 2px;
  }
  .contact {
    position: absolute; right: 28px; bottom: 34px;
    list-style: none; text-align: right;
    color: var(--ink-navy); font-size: 14px; line-height: 1.55;
  }
  .contact li { display: flex; justify-content: flex-end; align-items: center; gap: 8px; }
  .contact svg { width: 12px; height: 12px; flex: none; }
  /* Back */
  .card-back {
    left: 610px; top: 440px;
    background: linear-gradient(180deg, var(--back-top) 0%, var(--back-bottom) 100%);
    display: flex; align-items: center; justify-content: center;
  }
  .back-brand {
    color: var(--ink-navy); font-weight: 400; font-size: 40px; letter-spacing: 3px;
  }
</style>
</head>
<body>
<main class="canvas">
  <section class="card card-front" aria-label="Card front">
    <svg class="swoosh" viewBox="0 0 520 300" preserveAspectRatio="none" aria-hidden="true">
      <path d="M0 300 C 170 300, 240 260, 300 190 C 360 120, 420 95, 520 95 L520 300 Z" fill="var(--swoosh)"/>
      <path d="M40 300 C 200 300, 250 250, 310 185 C 360 132, 420 105, 520 102" fill="none" stroke="var(--swoosh-edge)" stroke-width="3"/>
    </svg>
    <div class="holder">
      <p class="holder-name">Peter Castrell</p>
      <p class="holder-title">President</p>
    </div>
    <p class="front-brand">Thornvale Group</p>
    <ul class="contact">
      <li>(555) 204-6391
        <svg viewBox="0 0 12 12"><path d="M2 1l2 0 1 3-1.3 1a6 6 0 0 0 3.3 3.3L8 7l3 1v2a1 1 0 0 1-1 1A9 9 0 0 1 1 2a1 1 0 0 1 1-1z" fill="var(--ink-navy)"/></svg>
      </li>
      <li>pc@thornvalegroup.example
        <svg viewBox="0 0 12 12"><rect x="1" y="2.5" width="10" height="7" rx="1" fill="none" stroke="var(--ink-navy)"/><path d="M1 3l5 3.5L11 3" fill="none" stroke="var(--ink-navy)"/></svg>
      </li>
      <li>www.thornvalegroup.example
        <svg viewBox="0 0 12 12"><circle cx="6" cy="6" r="5" fill="none" stroke="var(--ink-navy)"/><ellipse cx="6" cy="6" rx="2.2" ry="5" fill="none" stroke="var(--ink-navy)"/><path d="M1 6h10" stroke="var(--ink-navy)"/></svg>
      </li>
    </ul>
  </section>

  <section class="card card-back" aria-label="Card back">
    <p class="back-brand">Thornvale Group</p>
  </section>
</main>
</body>
</html>
```